New Flyer Design Project - for sale units at The Lodge phase 3

on attached the A2 is full kitchen 1 bedroom, the A3 is gally kitchen and the B2 is the the 2 bedroom, on attached pictures the room with 2 queen beds is only for the 2 bedroom

This is going to be used to sale the units (real estate sale) so the layout could possibly be text and then pictures maybe 1 bedroom on one side and 2 on the back?

Experience the Modern Luxury of the New Phase 3 Building of the
Lodge at Harper's Landing

* Opening Spring 2019

* America's #17 Family Resort; Tennessee's Only Ranked Resort

1 Bedroom Bunk Suite (Galley Kitchen) - $199,000; Sleeps 6

* Private King Master Bedroom

* Bunk Bed Galley

* Granite Counters Throughout

* Fully Furnished with Custom Furnishings

* Private Balcony

* Equipped Galley Kitchen

* In Unit Laundry

* Queen Sleeper Sofa

1 Bedroom Bunk Suite (Full Kitchen) - $209,000; Sleeps 6

* Bunk Bed Galley

* Granite Counters throughout

* Equipped Full Kitchen

* Completely Furnished with Custom Furnishings

* Private Balcony

* In Unit Laundry

* Queen Sleeper Sofa

2 Bedroom Bunk Suite (Full Kitchen) - $249,000; Sleeps 10

* Private King Master Bedroom with On-Suite Bathroom

* Two Queen Bedroom

* Bunk Bed Galley

* Full Kitchen

* Private Balcony

* In Unit Laundry

* Queen Sleeper Sofa

Target Market(s)

people wanting to buy units in phase 3 of The Lodge at governor's crossing

Industry/Entity Type

Real Estate Development

Requirements
Must have
• attached text to describe units and price
• pictures and layouts
• Contact Dale Fenton
• 865-555-0172 Dale@bluecedarretreats.example
Nice to have
• brand and logo
Should not have
• it should not be plain this is m ore of a luxury project

```html
<!DOCTYPE html>
<html lang="en">
<head>
<meta charset="utf-8">
<title>The Lodge at Harper's Landing – Phase 3 Suites</title>
<link href="https://fonts.googleapis.com/css2?family=Alegreya:ital,wght@1,700&family=Barlow+Semi+Condensed:wght@400;500;600&display=swap" rel="stylesheet">
<style>
  :root {
    --backdrop: #2b2b2d;
    --paper: #ffffff;
    --brown: #6b5340;
    --brown-deep: #4e3b2c;
    --gold: #d9a05b;
    --gold-deep: #b9843f;
    --gold-text: #e3aa62;
    --teal: #5f8893;
    --teal-deep: #4b7480;
    --teal-text: #3f7480;
    --ink-brown: #55402f;
    --green: #3f7d2c;
    --cream: #f4ede2;
  }
  * { margin: 0; padding: 0; box-sizing: border-box; }
  html, body { width: 1200px; height: 789px; overflow: hidden; }
  body {
    background: var(--backdrop);
    font-family: "Barlow Semi Condensed", "Arial Narrow", sans-serif;
    position: relative;
  }
  .page { position: absolute; top: 38px; height: 712px; overflow: hidden; }
  .page--front { left: 36px; width: 550px; background: var(--paper); }
  .page--plans { left: 614px; width: 550px; }

  .hero-photo {
    position: absolute; left: 0; top: 0; width: 550px; height: 278px;
    background: linear-gradient(135deg, #c9d39a 0%, #e6e2c8 35%, #f3f1ea 55%, #6a6f66 100%);
  }
  .thumb-strip {
    position: absolute; left: 14px; top: 278px; width: 523px; height: 166px;
    background: var(--gold);
  }
  .thumb { position: absolute; top: 8px; height: 114px; }
  .thumb--bed { left: 6px; width: 136px; background: linear-gradient(160deg, #b9c68c, #ece8dc 60%, #5b6a6a); }
  .thumb--dining { left: 148px; width: 148px; background: linear-gradient(160deg, #aab77e, #6f7166 55%, #4e5f60); }
  .thumb--kitchen { left: 302px; width: 112px; background: linear-gradient(160deg, #e6e0cf, #b9b3a2 50%, #3c3634); }
  .thumb--bunk { left: 420px; width: 96px; background: linear-gradient(160deg, #e9c99a, #f3e6cf 50%, #8f8a7e); }
  .thumb-strip__base { position: absolute; left: 0; bottom: 0; width: 100%; height: 44px; background: var(--paper); }

  .opening-banner {
    position: absolute; left: 108px; top: 408px; width: 332px; height: 48px;
  }
  .opening-banner svg { position: absolute; inset: 0; }
  .opening-banner__text {
    position: absolute; inset: 0; display: flex; align-items: center; justify-content: center;
    font-family: "Alegreya", Georgia, serif; font-style: italic; font-weight: 700;
    font-size: 31px; color: var(--gold-text);
  }
  .ranking {
    position: absolute; left: 0; top: 474px; width: 550px; text-align: center;
    font-family: "Alegreya", Georgia, serif; font-style: italic; font-weight: 700;
    font-size: 19px; color: var(--teal-text);
  }
  .award {
    position: absolute; left: 0; top: 503px; width: 550px;
    display: flex; justify-content: center; align-items: center; gap: 6px;
    font-size: 20px;
  }
  .award__badge { width: 40px; height: 18px; border-radius: 9px; background: #222; }
  .award__name { color: #222; font-weight: 400; }
  .award__title { font-family: "Alegreya", Georgia, serif; font-style: italic; font-weight: 700; color: var(--green); font-size: 18px; }

  .info-band {
    position: absolute; left: 0; top: 548px; width: 550px; height: 164px;
    background: var(--brown); color: var(--paper);
  }
  .info-band__lead {
    position: absolute; left: 32px; top: 18px; width: 320px;
    font-size: 18.5px; line-height: 19px; font-weight: 500;
  }
  .info-band__rule { position: absolute; left: 32px; top: 83px; width: 268px; height: 2px; background: #e9e2d8; }
  .contact { position: absolute; left: 32px; top: 93px; }
  .contact__label { font-size: 14px; line-height: 16px; }
  .contact__name { font-size: 19px; font-weight: 600; line-height: 22px; }
  .contact__email { font-size: 14.5px; line-height: 17px; }

  .brand {
    position: absolute; left: 340px; top: 50px; width: 200px;
    display: flex; align-items: center; gap: 10px;
    font-size: 20px; font-weight: 600; line-height: 22px; color: var(--gold-text);
  }
  .brand__mark { width: 14px; height: 14px; border-radius: 50%; background: var(--gold-text); flex: none; }

  .suite { position: absolute; left: 0; width: 550px; }
  .suite--galley { top: 0; height: 238px; background: var(--gold); color: var(--ink-brown); }
  .suite--full { top: 238px; height: 236px; background: var(--brown); color: var(--gold-text); }
  .suite--two { top: 474px; height: 238px; background: var(--teal); color: var(--paper); }
  .suite__chevron { position: absolute; left: 0; top: 0; width: 100px; height: 100%; }
  .suite--galley .suite__chevron { background: var(--gold-deep); }
  .suite--full .suite__chevron { background: var(--brown-deep); }
  .suite--two .suite__chevron { background: var(--teal-deep); }
  .suite__chevron { clip-path: polygon(0 0, 74px 0, 100px 50%, 74px 100%, 0 100%); }
  .suite__number {
    position: absolute; left: 14px; top: 50%; transform: translateY(-50%);
    font-size: 130px; font-weight: 600; line-height: 1; opacity: 0.28;
  }
  .suite--galley .suite__number { color: #8a5a25; }
  .suite--full .suite__number { color: #2e2219; opacity: 0.5; }
  .suite--two .suite__number { color: #7fa3ad; opacity: 0.5; }
  .floor-plan {
    position: absolute; left: 106px; width: 240px;
    border: 3px solid var(--paper);
    background: linear-gradient(135deg, #e4dccd 0%, #d6cbb8 50%, #e9e2d5 100%);
  }
  .suite--galley .floor-plan { top: 20px; height: 200px; }
  .suite--full .floor-plan { top: 18px; height: 200px; }
  .suite--two .floor-plan { top: 18px; height: 202px; }
  .suite__details { position: absolute; left: 365px; width: 180px; }
  .suite--galley .suite__details { top: 34px; }
  .suite--full .suite__details { top: 32px; }
  .suite--two .suite__details { top: 24px; }
  .suite__title { font-size: 15px; line-height: 17.5px; font-weight: 600; margin-bottom: 3px; }
  .suite__features { list-style: none; font-size: 11.2px; line-height: 14px; }
  .suite__features li { padding-left: 7px; text-indent: -7px; }
  .suite__features li::before { content: "• "; }
  .suite__features li span { display: block; text-indent: 0; }
</style>
</head>
<body>

<section class="page page--front">
  <div class="hero-photo" role="img" aria-label="Photo of a suite bedroom with king bed, green accent wall and bedside lamps"></div>

  <div class="thumb-strip">
    <div class="thumb-strip__base"></div>
    <div class="thumb thumb--bed" role="img" aria-label="Photo of the two queen bedroom"></div>
    <div class="thumb thumb--dining" role="img" aria-label="Photo of the living and dining area"></div>
    <div class="thumb thumb--kitchen" role="img" aria-label="Photo of the kitchen with granite counters"></div>
    <div class="thumb thumb--bunk" role="img" aria-label="Photo of the bunk bed galley"></div>
  </div>

  <div class="opening-banner">
    <svg width="332" height="48" viewBox="0 0 332 48" aria-hidden="true">
      <polygon points="0,0 332,0 314,48 18,48" fill="#6b5340"/>
    </svg>
    <div class="opening-banner__text">Opening Spring 2019</div>
  </div>

  <p class="ranking">America's #17 Family Resort - Tennessee's Only Ranked Resort</p>
  <p class="award">
    <span class="award__badge" aria-hidden="true"></span>
    <span class="award__name">TravelRank</span>
    <span class="award__title">Guest Favorite 2018</span>
  </p>

  <div class="info-band">
    <p class="info-band__lead">Experience the Modern Luxury of the New Phase 3 Building of the Lodge, at Harper's Landing</p>
    <div class="info-band__rule"></div>
    <div class="contact">
      <p class="contact__label">Contact:</p>
      <p class="contact__name">Dale Fenton | 865-555-0172</p>
      <p class="contact__email">Dale@bluecedarretreats.example</p>
    </div>
    <div class="brand">
      <span class="brand__mark" aria-hidden="true"></span>
      <span>The Lodge at Harper's Landing</span>
    </div>
  </div>
</section>

<section class="page page--plans">
  <article class="suite suite--galley">
    <div class="suite__chevron"><span class="suite__number">1</span></div>
    <div class="floor-plan" role="img" aria-label="Floor plan of the 1 bedroom bunk suite with galley kitchen"></div>
    <div class="suite__details">
      <h2 class="suite__title">1 Bedroom Bunk Suite<br>(Galley Kitchen)<br>$199,000 : Sleeps 6</h2>
      <ul class="suite__features">
        <li>Private King Master Bedroom</li>
        <li>Bunk Bed Galley</li>
        <li>Granite Counters Throughout</li>
        <li>Fully Furnished with Custom Furnishings</li>
        <li>Private Balcony</li>
        <li>Equipped Galley Kitchen</li>
        <li>In Unit Laundry</li>
        <li>Queen Sleeper Sofa</li>
      </ul>
    </div>
  </article>

  <article class="suite suite--full">
    <div class="suite__chevron"><span class="suite__number">1</span></div>
    <div class="floor-plan" role="img" aria-label="Floor plan of the 1 bedroom bunk suite with full kitchen"></div>
    <div class="suite__details">
      <h2 class="suite__title">1 Bedroom Bunk Suite<br>(Full Kitchen)<br>$209,000; Sleeps 6</h2>
      <ul class="suite__features">
        <li>Private King Master Bedroom</li>
        <li>Bunk Bed Galley</li>
        <li>Granite Counters throughout</li>
        <li>Equipped Full Kitchen</li>
        <li>Completely Furnished with Custom Furnishings</li>
        <li>Private Balcony</li>
        <li>In Unit Laundry</li>
        <li>Queen Sleeper Sofa</li>
      </ul>
    </div>
  </article>

  <article class="suite suite--two">
    <div class="suite__chevron"><span class="suite__number">2</span></div>
    <div class="floor-plan" role="img" aria-label="Floor plan of the 2 bedroom bunk suite with full kitchen"></div>
    <div class="suite__details">
      <h2 class="suite__title">2 Bedroom Bunk Suite<br>(Full Kitchen)<br>$249,000; Sleeps 10</h2>
      <ul class="suite__features">
        <li>Private King Master Bedroom with Ensuite Bathroom</li>
        <li>Two Queen Bedroom</li>
        <li>Bunk Bed Galley</li>
        <li>Granite Counters Throughout</li>
        <li>Full Kitchen</li>
        <li>Completely Furnished with Custom Furnishings</li>
        <li>Private Balcony</li>
        <li>In Unit Laundry</li>
        <li>Queen Sleeper Sofa</li>
      </ul>
    </div>
  </article>
</section>

</body>
</html>
```